Harbourline Electrical Solutions

On one side. LOGO (underneath:) Commercial Industrial Residential

- NAME & CONTACT DETAILS

Marcus T. Hollings
Project Manager

(Cell icon) (441) 555-0187
(Email icon) hlelectricalsolutions@mailvento.com
(Facebook & Instagram icons )@hlelectricalsolutions

Other side: LOGO - underneath ELECTRICAL CONSTRUCTION & MAINTENANCE . LED LIGHTING & AUTOMATION . LIFE SAFETY SYSTEMS (FIRE ALARM / SECURITY) . DATA & COMMUNICATION

```html
<!DOCTYPE html>
<html lang="en">
<head>
<meta charset="utf-8">
<title>Harbourline Electrical Solutions – Business Card</title>
<link rel="stylesheet" href="https://fonts.googleapis.com/css2?family=Poppins:ital,wght@0,400;0,500;0,600;0,700;1,400&display=swap">
<style>
  :root {
    --teal: #1a7f9c;
    --teal-dark: #0e5d76;
    --teal-deep: #0a4a60;
    --ink-grey: #4b4f53;
    --soft-grey: #8a8f94;
    --paper: #ffffff;
    --paper-shade: #eef0f1;
    --backdrop: #e7e4df;
  }
  * { box-sizing: border-box; margin: 0; padding: 0; }
  html, body { width: 1200px; height: 780px; overflow: hidden; }
  body {
    background: var(--backdrop);
    font-family: "Poppins", sans-serif;
    display: flex;
    flex-direction: column;
    align-items: center;
    justify-content: center;
    gap: 36px;
  }
  .card {
    width: 580px;
    height: 332px;
    border-radius: 4px;
    box-shadow: 0 6px 18px rgba(0,0,0,0.14);
    position: relative;
    overflow: hidden;
  }

  /* Front side */
  .card-front {
    background: linear-gradient(135deg, var(--paper) 0%, var(--paper-shade) 100%);
    padding: 34px 40px;
  }
  .brand {
    position: absolute;
    top: 34px;
    right: 40px;
    text-align: left;
  }
  .brand-lockup {
    display: flex;
    align-items: center;
    gap: 10px;
  }
  .brand-square {
    width: 16px;
    height: 16px;
    background: var(--teal);
    flex: none;
  }
  .brand-name {
    color: var(--teal);
    font-weight: 600;
    font-size: 19px;
    line-height: 1.15;
    letter-spacing: 0.5px;
  }
  .brand-tagline {
    margin-top: 8px;
    font-style: italic;
    font-size: 11.5px;
    color: var(--ink-grey);
    letter-spacing: 0.6px;
  }
  .person {
    position: absolute;
    left: 40px;
    top: 150px;
  }
  .person-name {
    color: var(--teal);
    font-weight: 700;
    font-size: 17px;
    letter-spacing: 1px;
    text-transform: uppercase;
  }
  .person-role {
    color: var(--ink-grey);
    font-size: 13px;
    margin-top: 1px;
  }
  .contact {
    position: absolute;
    left: 40px;
    right: 40px;
    top: 214px;
    color: var(--ink-grey);
    font-size: 13px;
  }
  .contact-row {
    display: flex;
    align-items: center;
    gap: 6px;
    height: 22px;
  }
  .icon-badge {
    width: 17px;
    height: 17px;
    border-radius: 50%;
    background: var(--teal);
    display: inline-flex;
    align-items: center;
    justify-content: center;
    flex: none;
  }
  .icon-plain {
    width: 17px;
    height: 17px;
    border-radius: 50%;
    background: var(--teal);
    flex: none;
  }
  .contact-divider {
    height: 1px;
    width: 330px;
    margin: 6px 0 8px;
    background: linear-gradient(90deg, rgba(26,127,156,0.15), var(--teal), rgba(26,127,156,0.15));
  }

  /* Back side */
  .card-back {
    background: radial-gradient(ellipse at 70% 35%, var(--teal) 0%, var(--teal-dark) 55%, var(--teal-deep) 100%);
    color: var(--paper);
    display: flex;
    flex-direction: column;
    align-items: center;
    justify-content: center;
    gap: 34px;
  }
  .back-brand {
    display: flex;
    align-items: center;
    gap: 14px;
  }
  .back-brand .brand-square { width: 22px; height: 22px; background: var(--paper); }
  .back-brand .brand-name {
    color: var(--paper);
    font-size: 30px;
    font-weight: 600;
    line-height: 1.1;
  }
  .services {
    text-align: center;
    font-size: 12px;
    line-height: 1.7;
    letter-spacing: 0.3px;
  }
</style>
</head>
<body>

  <section class="card card-front" aria-label="Card front">
    <div class="brand">
      <div class="brand-lockup">
        <span class="brand-square"></span>
        <div class="brand-name">Harbourline<br>Electrical Solutions</div>
      </div>
      <p class="brand-tagline">Commercial Industrial Residential</p>
    </div>

    <div class="person">
      <h1 class="person-name">Marcus T. Hollings</h1>
      <p class="person-role">Project Manager</p>
    </div>

    <div class="contact">
      <div class="contact-row">
        <span class="icon-badge" aria-label="Phone">
          <svg width="9" height="9" viewBox="0 0 24 24"><path fill="#fff" d="M6.6 10.8a15.1 15.1 0 0 0 6.6 6.6l2.2-2.2a1 1 0 0 1 1-.25 11.4 11.4 0 0 0 3.6.57 1 1 0 0 1 1 1V20a1 1 0 0 1-1 1A17 17 0 0 1 3 4a1 1 0 0 1 1-1h3.5a1 1 0 0 1 1 1c0 1.25.2 2.45.57 3.57a1 1 0 0 1-.25 1z"/></svg>
        </span>
        <span class="icon-badge" aria-label="Email">
          <svg width="9" height="9" viewBox="0 0 24 24"><rect x="2" y="5" width="20" height="14" rx="2" fill="#fff"/><path d="M3 6l9 7 9-7" fill="none" stroke="#1a7f9c" stroke-width="2"/></svg>
        </span>
        <span>(441) 555-0187</span>
      </div>
      <div class="contact-row">
        <span>hlelectricalsolutions@mailvento.com</span>
      </div>
      <div class="contact-divider"></div>
      <div class="contact-row">
        <span class="icon-plain"></span>
        <span>@hlelectricalsolutions</span>
      </div>
    </div>
  </section>

  <section class="card card-back" aria-label="Card back">
    <div class="back-brand">
      <span class="brand-square"></span>
      <div class="brand-name">Harbourline<br>Electrical Solutions</div>
    </div>
    <p class="services">
      Electrical Construction &amp; Maintenance | LED Lighting &amp; Automation<br>
      Life Safety Systems (FIRE ALARM / SECURITY) | Data &amp; Communication
    </p>
  </section>

</body>
</html>
```